Web Developer Needs a Business Card Design

I need a personal business card design that represents me as a web developer for potential employers. I would like the background to be a dark color on the front for contrast with my logo and name. The back will have all my information along with a smaller version of the logo. I want something with a modern look and feel, not too conservative. This will be used for potential employers and freelance work.

Industry/Entity Type

Business

Contact Information for Business Card

Front should have my logo and name. The back should have all my personal information which would include: name: Tom Varulek, phone: 570-614-3098, email: tomvarulek@quillbox.net, website url: www.tomvarulek.net, logo, web developer.

Font styles to use
Sans Serif

Requirements
Must have
• Must include my logo. The color palette base color will be the logo color.

```html
<!DOCTYPE html>
<html lang="en">
<head>
<meta charset="utf-8">
<title>Tom Varulek — Business Card</title>
<link rel="stylesheet" href="https://fonts.googleapis.com/css2?family=Open+Sans:wght@400;600;700&display=swap">
<style>
  :root {
    --backdrop: #1b1b1b;
    --card-black: #0b0b0b;
    --card-black-sheen: #1e1e1e;
    --brand-teal: #8fd3c2;
    --brand-teal-light: #b5e6da;
    --text-white: #f4f4f4;
    --text-dark: #1d2a27;
    --divider: #4d6e66;
  }
  * { box-sizing: border-box; margin: 0; padding: 0; }
  html, body {
    width: 1200px;
    height: 864px;
    overflow: hidden;
    background: var(--backdrop);
    font-family: "Open Sans", sans-serif;
  }
  .card-set {
    width: 1200px;
    height: 864px;
    display: flex;
    align-items: center;
    justify-content: center;
    gap: 56px;
  }
  .card {
    width: 520px;
    height: 297px;
    border-radius: 4px;
    overflow: hidden;
    position: relative;
    box-shadow: 0 18px 40px rgba(0, 0, 0, 0.6);
  }
  .card--front {
    background: linear-gradient(150deg, var(--card-black-sheen) 0%, var(--card-black) 55%);
    display: flex;
    flex-direction: column;
    align-items: center;
    justify-content: center;
  }
  .brand-mark {
    width: 52px;
    height: 52px;
    border-radius: 50%;
    border: 3px solid var(--brand-teal);
    background: var(--card-black);
  }
  .brand-name {
    margin-top: 10px;
    color: var(--text-white);
    font-size: 25px;
    font-weight: 400;
    letter-spacing: 0.5px;
  }
  .card--back { display: flex; flex-direction: column; }
  .back-header {
    height: 160px;
    background: linear-gradient(150deg, var(--card-black-sheen) 0%, var(--card-black) 55%);
    display: flex;
    flex-direction: column;
    align-items: center;
    justify-content: center;
    padding-top: 8px;
  }
  .back-header .brand-mark { width: 44px; height: 44px; }
  .back-header .brand-name { font-size: 22px; margin-top: 8px; }
  .back-details {
    flex: 1;
    background: linear-gradient(120deg, var(--brand-teal) 0%, var(--brand-teal-light) 70%, var(--brand-teal) 100%);
    display: flex;
    align-items: center;
    justify-content: center;
    padding-left: 40px;
  }
  .identity {
    text-align: right;
    padding-right: 18px;
    color: var(--text-dark);
  }
  .identity-name { font-size: 15px; font-weight: 700; }
  .identity-role { font-size: 12px; font-weight: 600; margin-top: 1px; }
  .details-divider {
    width: 1px;
    height: 100px;
    background: var(--divider);
  }
  .contact-list {
    list-style: none;
    padding-left: 14px;
    color: var(--text-dark);
    font-size: 12.5px;
  }
  .contact-item {
    display: flex;
    align-items: center;
    gap: 8px;
    line-height: 19px;
  }
  .contact-icon { width: 13px; height: 13px; flex: none; }
</style>
</head>
<body>
<main class="card-set">
  <section class="card card--front" aria-label="Card front">
    <span class="brand-mark" aria-hidden="true"></span>
    <h1 class="brand-name">TOM VARULEK</h1>
  </section>

  <section class="card card--back" aria-label="Card back">
    <div class="back-header">
      <span class="brand-mark" aria-hidden="true"></span>
      <h2 class="brand-name">TOM VARULEK</h2>
    </div>
    <div class="back-details">
      <div class="identity">
        <p class="identity-name">Tom Varulek</p>
        <p class="identity-role">Web Developer</p>
      </div>
      <span class="details-divider" aria-hidden="true"></span>
      <ul class="contact-list">
        <li class="contact-item">
          <svg class="contact-icon" viewBox="0 0 16 16" aria-hidden="true"><path d="M4 1.5 6.3 4.5 5 6.3c.9 1.9 2.6 3.6 4.7 4.7l1.8-1.3 3 2.3-1.3 2.3C8 14 2 8 1.7 3z" fill="#1d2a27"/></svg>
          (570) 614-3098
        </li>
        <li class="contact-item">
          <svg class="contact-icon" viewBox="0 0 16 16" aria-hidden="true"><rect x="1" y="3" width="14" height="10" rx="1" fill="none" stroke="#1d2a27" stroke-width="1.6"/><path d="M1.5 3.8 8 9l6.5-5.2" fill="none" stroke="#1d2a27" stroke-width="1.6"/></svg>
          tomvarulek@quillbox.net
        </li>
        <li class="contact-item">
          <svg class="contact-icon" viewBox="0 0 16 16" aria-hidden="true"><circle cx="8" cy="8" r="6.5" fill="none" stroke="#1d2a27" stroke-width="1.4"/><ellipse cx="8" cy="8" rx="2.8" ry="6.5" fill="none" stroke="#1d2a27" stroke-width="1.2"/><path d="M1.5 8h13" stroke="#1d2a27" stroke-width="1.2"/></svg>
          www.tomvarulek.net
        </li>
      </ul>
    </div>
  </section>
</main>
</body>
</html>
```